Business Card Design Project

I need a business card designed from scratch. I have an existing logo that I can upload in Illustrator for modification or redesign.

The Company is called Query Lanterns http://querylanterns.com.au and we provide Search Engine Optimization services to Australian businesses. The current logo signifies an increase in visitors, profits etc...

There are no restrictions as to the redesign - colours, style etc are all open to change.

Cards will be full colour and one sided printed at http://www.cardmoxel.com.au so check their requirements for file format and sizes etc.

I will expect all original files upon completion of project.

Target Market(s)

Any business with a web site looking to improve their search engine rankings

Industry/Entity Type

Business

Requirements
Must have
• I like modern, sleek designs. Clean, not fussy, uncluttered.

```html
<!DOCTYPE html>
<html lang="en">
<head>
<meta charset="utf-8">
<title>Query Lanterns – Business Card</title>
<link rel="stylesheet" href="https://fonts.googleapis.com/css2?family=Open+Sans:wght@400;600;700;800&display=swap">
<style>
  :root {
    --page: #e8e5e1;
    --card: #ffffff;
    --brand-blue: #1f6fb8;
    --band-dark: #163f78;
    --band-light: #2b63a8;
    --rule: #1b3a66;
    --ink: #3a3a3a;
    --ink-soft: #555555;
    --accent-yellow: #f5c518;
    --divider: #c9c9c9;
  }
  * { margin: 0; padding: 0; box-sizing: border-box; }
  html, body {
    width: 1200px; height: 412px; overflow: hidden;
    background: var(--page);
    font-family: "Open Sans", Arial, sans-serif;
  }
  .stage { position: relative; width: 1200px; height: 412px; }
  .card {
    position: absolute; top: 64px; width: 496px; height: 284px;
    background: var(--card);
    box-shadow: 0 3px 10px rgba(0,0,0,0.25);
  }
  .card--front { left: 73px; }
  .card--back { left: 631px; }

  .brand {
    position: absolute; left: 0; right: 0; top: 58px;
    display: flex; justify-content: center; align-items: center; gap: 10px;
  }
  .brand__dot {
    width: 16px; height: 16px; border-radius: 50%;
    background: var(--accent-yellow);
  }
  .brand__name {
    font-weight: 800; font-size: 30px; color: var(--brand-blue);
    letter-spacing: -0.5px; line-height: 1;
  }

  .band-rule {
    position: absolute; left: 0; right: 0; height: 2px; background: var(--rule);
  }
  .band-rule--top { top: 146px; }
  .band-rule--bottom { top: 189px; }
  .name-band {
    position: absolute; left: 0; right: 0; top: 151px; height: 35px;
    background: linear-gradient(90deg, var(--band-dark) 0%, var(--band-light) 50%, var(--band-dark) 100%);
    color: #fff; display: flex; align-items: center; justify-content: center;
    font-size: 15px;
  }
  .name-band__name { font-weight: 700; }
  .name-band__title { font-weight: 400; margin-left: 5px; }

  .address {
    position: absolute; right: 291px; top: 220px;
    text-align: right; font-size: 12px; line-height: 17px; color: var(--ink);
  }
  .contact-divider {
    position: absolute; left: 231px; top: 210px; width: 1px; height: 52px;
    background: var(--divider);
  }
  .contacts {
    position: absolute; left: 256px; top: 210px; list-style: none;
    font-size: 12px; line-height: 17px; color: var(--ink);
  }
  .contacts li { display: flex; align-items: center; gap: 6px; }
  .contacts svg { width: 10px; height: 10px; fill: var(--ink-soft); }

  .brand--large { top: 108px; gap: 14px; }
  .brand--large .brand__dot { width: 24px; height: 24px; }
  .brand--large .brand__name { font-size: 44px; }
  .web {
    position: absolute; left: 0; right: 0; top: 255px; text-align: center;
    font-size: 12px; font-weight: 700; letter-spacing: 4px; color: var(--ink);
  }
</style>
</head>
<body>
<main class="stage">
  <section class="card card--front" aria-label="Card front">
    <div class="brand">
      <span class="brand__dot"></span>
      <span class="brand__name">Query Lanterns</span>
    </div>
    <div class="band-rule band-rule--top"></div>
    <div class="name-band">
      <span class="name-band__name">Your Name /</span>
      <span class="name-band__title">Title</span>
    </div>
    <div class="band-rule band-rule--bottom"></div>

    <address class="address" style="font-style:normal">
      Complex name,Street name<br>
      City, State, zip code
    </address>
    <div class="contact-divider"></div>
    <ul class="contacts">
      <li>
        <svg viewBox="0 0 10 10" aria-hidden="true"><path d="M2 0.5 L3.6 0.5 L4.2 2.8 L3 3.6 C3.6 5 4.9 6.3 6.4 7 L7.2 5.8 L9.5 6.4 L9.5 8 C9.5 9 8.6 9.6 7.6 9.4 C4 8.6 1.4 6 0.6 2.4 C0.4 1.4 1 0.5 2 0.5 Z"/></svg>
        098 765 4321
      </li>
      <li>
        <svg viewBox="0 0 10 10" aria-hidden="true"><path d="M3 0 H7 A1 1 0 0 1 8 1 V9 A1 1 0 0 1 7 10 H3 A1 1 0 0 1 2 9 V1 A1 1 0 0 1 3 0 Z M3 1.5 V7 H7 V1.5 Z M4.4 8 H5.6 V8.8 H4.4 Z"/></svg>
        098 765 4321
      </li>
      <li>
        <svg viewBox="0 0 10 10" aria-hidden="true"><path d="M0.5 2 H9.5 V8.5 H0.5 Z M1.3 2.8 L5 5.6 L8.7 2.8 V2.6 H1.3 Z" fill-rule="evenodd"/></svg>
        enquiry@querylanterns.com.au
      </li>
    </ul>
  </section>

  <section class="card card--back" aria-label="Card back">
    <div class="brand brand--large">
      <span class="brand__dot"></span>
      <span class="brand__name">Query Lanterns</span>
    </div>
    <p class="web">www.querylanterns.com.au</p>
  </section>
</main>
</body>
</html>
```